International business needs business cards

Our company, DRV Ventures Inc. is in the business of supplying a range construction products with particular emphasis on CEMENT. We have developed our own brand - TORVAN SUPPLIES - with which to infiltrate the market. We are launching our brand of cement (TORVAN Type IS Cement) into the Caribbean which is unlike anything this market has ever seen. A monopoly has existed here for the past 60-odd years and the market has now opened to allow the importation of other brands and consumers are anxious and ready for change/improvement. We are very excited to be launching and want to make a great first impression. We will be conducting workshops and seminars (from government level to the hardware store owners) and we want our business card to give us the strong, confident introduction that we need.

Target Market(s)

construction; builders; engineers; home owners

Industry/Entity Type

Construction

Contact Information for Business Card

Marisol Depree
CEO
cell # 1 555 4180736
Ground floor,Lindell Plaza Suite 2734
George Town,Grand Cayman
Cayman Islands,KY1-4823
EMAIL: m.depree@drvventuresinc.example
web site drvventuresinc.example

COMPANY: skype info drv.ventures.example

second card
Yvette Brannock-Depree
CFO
CELL# 1 555 607 3941
George Town,Grand Cayman
Cayman Islands,KY1-4823
EMAIL: y.brannockdepree@drvventuresinc.example
website drvventuresinc.example

Requirements
Must have
• Business cards must display BOTH logos - DRV is the company and TORVAN is the brand.

```html
<!DOCTYPE html>
<html lang="en">
<head>
<meta charset="utf-8">
<title>DRV Ventures Inc. — Business Card</title>
<link rel="stylesheet" href="https://fonts.googleapis.com/css2?family=Source+Sans+3:wght@400;600&display=swap">
<style>
  :root {
    --backdrop: #9a9a9a;
    --card-light: #f1f1f1;
    --card-dark: #000000;
    --brand-red: #7a1416;
    --ink: #1e1e1e;
    --ink-soft: #555555;
    --brand-grey: #3a3a3a;
    --web-light: #dcdcdc;
  }
  html, body {
    margin: 0;
    padding: 0;
    overflow: hidden;
  }
  body {
    width: 1105px;
    height: 1200px;
    background: var(--backdrop);
    font-family: "Source Sans 3", "Myriad Pro", Arial, sans-serif;
    position: relative;
  }
  .card {
    position: absolute;
    left: 182px;
    width: 747px;
    height: 427px;
    box-sizing: border-box;
  }
  .card--front { top: 119px; background: var(--card-light); }
  .card--back  { top: 637px; background: var(--card-dark); }

  .brand-mark {
    position: absolute;
    top: 110px;
    right: 40px;
    display: flex;
    align-items: center;
    gap: 12px;
  }
  .brand-mark__dot {
    width: 22px;
    height: 22px;
    border-radius: 50%;
    background: var(--brand-grey);
  }
  .brand-mark__name {
    font-size: 34px;
    font-weight: 600;
    letter-spacing: 3px;
    color: var(--brand-grey);
  }

  .accent-bar {
    position: absolute;
    left: 0;
    top: 228px;
    width: 10px;
    height: 61px;
    background: var(--brand-red);
  }
  .holder {
    position: absolute;
    left: 29px;
    top: 228px;
  }
  .holder__name {
    margin: 0;
    font-size: 28px;
    font-weight: 600;
    line-height: 34px;
    color: var(--brand-red);
  }
  .holder__title {
    margin: 0;
    font-size: 20px;
    line-height: 26px;
    color: var(--ink);
  }
  .address, .contact {
    position: absolute;
    top: 298px;
    margin: 0;
    font-size: 19.5px;
    line-height: 27.5px;
    color: var(--ink-soft);
    font-style: normal;
  }
  .address { left: 29px; }
  .contact { left: 334px; top: 325px; }
  .contact__label { color: var(--brand-red); font-weight: 600; }

  .company-mark {
    position: absolute;
    top: 124px;
    left: 0;
    right: 0;
    display: flex;
    justify-content: center;
    align-items: center;
    gap: 18px;
  }
  .company-mark__square {
    width: 90px;
    height: 90px;
    background: var(--brand-red);
  }
  .company-mark__name {
    font-size: 60px;
    font-weight: 600;
    letter-spacing: 4px;
    color: #ffffff;
  }
  .web {
    position: absolute;
    top: 364px;
    left: 0;
    right: 0;
    margin: 0;
    text-align: center;
    font-size: 19px;
    letter-spacing: 3.6px;
    color: var(--web-light);
  }
</style>
</head>
<body>
  <section class="card card--front" aria-label="Business card front">
    <div class="brand-mark">
      <span class="brand-mark__dot"></span>
      <span class="brand-mark__name">TORVAN</span>
    </div>
    <div class="accent-bar"></div>
    <div class="holder">
      <h1 class="holder__name">Marisol Depree</h1>
      <p class="holder__title">CEO</p>
    </div>
    <address class="address">
      Ground floor<br>
      Lindell Plaza Suite 2734<br>
      George Town,Grand Cayman<br>
      Cayman Islands,KY1-4823
    </address>
    <p class="contact">
      <span class="contact__label">Mobile:</span>1 555 4180736<br>
      m.depree@drvventuresinc.example<br>
      www.drvventuresinc.example
    </p>
  </section>

  <section class="card card--back" aria-label="Business card back">
    <div class="company-mark">
      <span class="company-mark__square"></span>
      <span class="company-mark__name">DRV</span>
    </div>
    <p class="web">www.drvventuresinc.example</p>
  </section>
</body>
</html>
```